MRT Property - Business Cards

Looking for a business card & general letterhead, signage etc design for our new logo.

Colours:
000a20
0056a2
00b5ef
0088ce
68cef2

Fonts:
Poppins
Karla

Please keep look and feel of new brand - example in the zip package I sent.

```html
<!DOCTYPE html>
<html lang="en">
<head>
<meta charset="utf-8">
<title>MRT Property – Business Cards</title>
<link href="https://fonts.googleapis.com/css2?family=Karla:wght@400;500;700&family=Poppins:wght@400;600;700&display=swap" rel="stylesheet">
<style>
  :root {
    --ink-navy: #000a20;
    --card-navy: #0e1429;
    --deep-blue: #0056a2;
    --sky-blue: #00b5ef;
    --mid-blue: #0088ce;
    --pale-blue: #68cef2;
    --paper: #ffffff;
    --text-grey: #3a3a3a;
    --stage: #3d3d3d;
  }
  * { box-sizing: border-box; margin: 0; padding: 0; }
  html, body {
    width: 1200px; height: 803px; overflow: hidden;
    background: var(--stage);
  }
  .stage {
    position: relative; width: 1200px; height: 803px;
    display: flex; align-items: center; justify-content: center; gap: 60px;
  }
  .card {
    position: relative; width: 520px; height: 300px;
    border-radius: 22px; overflow: hidden;
  }
  /* Front */
  .card-front { background: var(--paper); }
  .card-front .swoosh { position: absolute; inset: 0; width: 100%; height: 100%; }
  .brand {
    position: absolute; top: 30px; right: 34px;
    display: flex; align-items: center; gap: 10px;
    font-family: "Poppins", sans-serif; font-weight: 700;
    font-size: 30px; color: var(--deep-blue); letter-spacing: 0.5px;
  }
  .brand-dot {
    width: 22px; height: 22px; border-radius: 50%;
    background: var(--mid-blue);
  }
  .contact {
    position: absolute; top: 92px; right: 34px;
    text-align: right; font-family: "Karla", sans-serif;
    font-size: 11.5px; line-height: 1.35; color: var(--text-grey);
  }
  .contact .address { margin-bottom: 8px; }
  .contact li { list-style: none; display: flex; justify-content: flex-end; align-items: center; gap: 6px; }
  .contact .icon { width: 10px; height: 10px; fill: var(--deep-blue); }
  .person {
    position: absolute; left: 78px; bottom: 92px;
    font-family: "Poppins", sans-serif;
  }
  .person-name { font-weight: 700; font-size: 22px; color: var(--deep-blue); line-height: 1.1; }
  .person-title { font-weight: 400; font-size: 12px; color: var(--sky-blue); margin-left: 18px; }
  /* Back */
  .card-back {
    background: var(--card-navy);
    display: flex; flex-direction: column; align-items: center; justify-content: center;
  }
  .back-brand {
    font-family: "Poppins", sans-serif; font-weight: 700;
    font-size: 44px; color: var(--pale-blue); letter-spacing: 1px;
    margin-top: -10px;
  }
  .back-web {
    position: absolute; bottom: 38px; left: 0; right: 0; text-align: center;
    font-family: "Karla", sans-serif; font-size: 13px; color: var(--paper);
    letter-spacing: 0.3px;
  }
</style>
</head>
<body>
<main class="stage">
  <section class="card card-front" aria-label="Business card front">
    <svg class="swoosh" viewBox="0 0 520 300" preserveAspectRatio="none" aria-hidden="true">
      <rect x="0" y="0" width="520" height="300" fill="var(--deep-blue)"/>
      <path d="M0 150 C40 200 70 260 110 300 L0 300 Z" fill="var(--sky-blue)"/>
      <ellipse cx="330" cy="90" rx="330" ry="200" fill="var(--paper)"/>
      <path d="M10 150 C20 230 80 280 150 300" stroke="var(--paper)" stroke-width="3" fill="none"/>
    </svg>
    <div class="brand"><span class="brand-dot"></span>MRT Property</div>
    <div class="contact">
      <p class="address">412 Harbour View Road<br>Halifax, Canada 20418</p>
      <ul>
        <li>555-210-4417
          <svg class="icon" viewBox="0 0 10 10"><path d="M2 0h2l1 3-1.5 1a6 6 0 0 0 2.5 2.5L7 5l3 1v2a2 2 0 0 1-2 2A8 8 0 0 1 0 2a2 2 0 0 1 2-2z"/></svg></li>
        <li>555-210-8832
          <svg class="icon" viewBox="0 0 10 10"><rect x="2" y="0" width="6" height="10" rx="1"/></svg></li>
        <li>info@mrtproperty.com
          <svg class="icon" viewBox="0 0 10 10"><path d="M0 2h10v6H0z M0 2l5 3.5L10 2" stroke="#fff" stroke-width="0.6"/></svg></li>
        <li>www.mrtproperty.com
          <svg class="icon" viewBox="0 0 10 10"><circle cx="5" cy="5" r="5"/></svg></li>
      </ul>
    </div>
    <div class="person">
      <p class="person-name">Daniel Reyes</p>
      <p class="person-title">President</p>
    </div>
  </section>

  <section class="card card-back" aria-label="Business card back">
    <p class="back-brand">MRT Property</p>
    <p class="back-web">www.mrtproperty.com</p>
  </section>
</main>
</body>
</html>
```